Now Leasing Banner

Looking for a banner that says the following information approx 4' x 30'

Now Leasing Maplebrook Terrace 925-318-6042

Target Market(s)

Drive by traffic

Industry/Entity Type

Residential property management

Requirements
Must have
• Clear and readable from a distance

```html
<!DOCTYPE html>
<html lang="en">
<head>
<meta charset="UTF-8">
<title>Now Leasing Banner – Maplebrook Terrace</title>
<link rel="stylesheet" href="https://fonts.googleapis.com/css2?family=Bebas+Neue&family=Fredoka:wght@600&family=Gochi+Hand&display=swap">
<style>
  :root {
    --canvas-bg: #eceef0;
    --banner-pink: #fbe3e8;
    --banner-green: #99a94b;
    --headline-red: #e2342f;
    --headline-navy: #263a7a;
    --contact-navy: #2b2f78;
    --photo-tone-light: #c9b89a;
    --photo-tone-deep: #a8946f;
    --key-photo-tone: #cfa48c;
  }
  * { margin: 0; padding: 0; box-sizing: border-box; }
  html, body {
    width: 800px;
    height: 1200px;
    overflow: hidden;
    background: var(--canvas-bg);
  }
  .canvas {
    position: relative;
    width: 800px;
    height: 1200px;
  }
  .banner {
    position: absolute;
    left: 305px;
    top: 17px;
    width: 190px;
    height: 1166px;
    overflow: hidden;
    box-shadow: 0 4px 14px rgba(0,0,0,0.18);
  }
  .banner-fields {
    position: absolute;
    inset: 0;
    width: 100%;
    height: 100%;
  }
  .property-photo {
    position: absolute;
    left: 0;
    top: 0;
    width: 190px;
    height: 180px;
    background: linear-gradient(180deg, var(--photo-tone-light), var(--photo-tone-deep));
  }
  .rotated {
    position: absolute;
    transform: translate(-50%, -50%) rotate(-90deg);
    white-space: nowrap;
    text-align: center;
  }
  .headline {
    left: 83px;
    top: 422px;
    width: 460px;
    font-family: "Bebas Neue", "Arial Narrow", sans-serif;
    font-size: 108px;
    font-weight: 400;
    line-height: 1;
    color: var(--headline-red);
    text-shadow: 3px -4px 0 var(--headline-navy);
  }
  .property-name {
    left: 54px;
    top: 895px;
    width: 280px;
    font-family: "Gochi Hand", cursive;
    font-size: 38px;
    line-height: 1;
    color: var(--contact-navy);
  }
  .phone {
    left: 128px;
    top: 880px;
    width: 340px;
    font-family: "Fredoka", sans-serif;
    font-weight: 600;
    font-size: 52px;
    line-height: 1;
    color: var(--contact-navy);
  }
  .key-photo {
    position: absolute;
    left: 0;
    top: 1050px;
    width: 90px;
    height: 100px;
    background: var(--key-photo-tone);
  }
</style>
</head>
<body>
  <main class="canvas">
    <section class="banner" aria-label="Now Leasing banner">
      <svg class="banner-fields" viewBox="0 0 190 1166" preserveAspectRatio="none" aria-hidden="true">
        <polygon points="0,180 190,180 190,626 0,731" fill="var(--banner-pink)"/>
        <polygon points="0,731 190,626 190,1166 0,1166" fill="var(--banner-green)"/>
      </svg>
      <div class="property-photo" role="img" aria-label="Photo of the apartment building exterior"></div>
      <h1 class="rotated headline">NOW LEASING</h1>
      <p class="rotated property-name">Maplebrook Terrace</p>
      <p class="rotated phone">925-318-6042</p>
      <div class="key-photo" role="img" aria-label="Photo of a hand holding out a house key"></div>
    </section>
  </main>
</body>
</html>
```